Lawn Sign Design – Brisqel

We need a clean, eye-catching 18" x 24" lawn sign for Brisqel that effectively communicates our core message while maintaining strong brand consistency.

Key Elements to Include:
Tagline (Main Focus): Upgrade Your Roof Without Replacing It
Website: www.trybrisqel.com
Phone Number: (888) BRISQEL-GO
TWQB License Number: 4480512
Brisqel Logo & Branding: Ensure the logo, corporate colors, and custom font are used consistently to align with our existing branding.

Design Guidelines:
Simple & High-Impact: The tagline should be the most prominent element on the sign, drawing immediate attention.
Easy Readability: Use a bold, clean design with high contrast for quick readability from a distance.
Balanced Layout: Place supporting details (website, phone number, and TWQB number) in a visually clear but secondary position to the tagline.
Professional & Modern: The sign should reflect credibility and innovation in the roofing industry.

Deliverables:
High-resolution print-ready files (CMYK)
A digital proof for review before finalizing
The final design should make a strong impression with minimal text, ensuring that anyone passing by can instantly grasp what we offer.

I am including our custom font. To get an hexagon in our name, simply type the $ after the 'O" Please use this font for anything you type.

```html
<!DOCTYPE html>
<html lang="en">
<head>
<meta charset="utf-8">
<title>Brisqel Lawn Sign</title>
<link rel="stylesheet" href="https://fonts.googleapis.com/css2?family=Poppins:wght@500;600;700;800&family=Mr+Dafoe&display=swap">
<style>
  :root {
    --backdrop: #9a9a9a;
    --charcoal: #2b2e33;
    --brand-blue: #0f3a88;
    --accent-blue: #1a51a0;
    --ink: #161616;
    --white: #ffffff;
  }
  * { margin: 0; padding: 0; box-sizing: border-box; }
  html, body {
    width: 1200px; height: 1200px; overflow: hidden;
    background: var(--backdrop);
    font-family: "Poppins", sans-serif;
  }
  .sign {
    position: absolute; left: 205px; top: 73px;
    width: 789px; height: 1052px;
    background: var(--white);
    overflow: hidden;
  }
  .sign__header {
    position: absolute; left: 0; top: 0; width: 789px; height: 740px;
    background: var(--charcoal);
  }
  .sign__panel { position: absolute; left: 0; top: 0; }
  .sign__text {
    position: absolute; left: 0; width: 100%;
    text-align: center; color: var(--white); line-height: 1;
  }
  .brand-name {
    top: 215px; font-size: 62px; font-weight: 600; letter-spacing: 2px;
  }
  .tagline-top {
    top: 314px; font-size: 62px; font-weight: 700; letter-spacing: -0.5px;
  }
  .tagline-main {
    top: 368px; font-size: 150px; font-weight: 700; letter-spacing: -3px;
  }
  .tagline-script {
    top: 498px; font-family: "Mr Dafoe", cursive; font-size: 72px;
    padding-left: 30px;
  }
  .tagline-bottom {
    top: 566px; font-size: 60px; font-weight: 700; letter-spacing: -0.5px;
  }
  .call-badge { position: absolute; left: 347px; top: 690px; }
  .contact-phone {
    position: absolute; left: 0; top: 800px; width: 100%;
    text-align: center; font-size: 56px; font-weight: 700;
    color: var(--ink); line-height: 1; letter-spacing: -0.5px;
  }
  .contact-web {
    position: absolute; left: 0; top: 876px; width: 100%;
    text-align: center; font-size: 46px; font-weight: 600;
    color: var(--ink); line-height: 1; letter-spacing: 4px;
  }
  .contact-web__domain { color: var(--accent-blue); }
  .license {
    position: absolute; left: 192px; top: 951px;
    width: 404px; height: 38px; border-radius: 5px;
    background: var(--accent-blue); color: var(--white);
    font-size: 20px; font-weight: 500;
    display: flex; align-items: center; justify-content: center;
  }
</style>
</head>
<body>
  <main class="sign">
    <div class="sign__header" role="img" aria-label="Dark charcoal background with soft roof-shingle wave texture"></div>
    <svg class="sign__panel" width="789" height="760" viewBox="0 0 789 760" aria-hidden="true">
      <polygon points="43,43 745,43 745,635 394,737 43,635" fill="var(--brand-blue)" stroke="var(--white)" stroke-width="2"/>
    </svg>

    <div class="sign__text brand-name">BRISQEL</div>
    <h1>
      <span class="sign__text tagline-top">UPGRADE YOUR</span>
      <span class="sign__text tagline-main">ROOF</span>
      <span class="sign__text tagline-script">Without</span>
      <span class="sign__text tagline-bottom">REPLACING IT</span>
    </h1>

    <svg class="call-badge" width="94" height="94" viewBox="0 0 94 94" aria-label="Phone">
      <circle cx="47" cy="47" r="43" fill="var(--white)" stroke="var(--accent-blue)" stroke-width="6"/>
      <path d="M33 30c2-2 4-2 5 0l4 6c1 2 0 3-1 4l-2 2c2 5 6 9 11 11l2-2c1-1 2-2 4-1l6 4c2 1 2 3 0 5l-3 3c-3 2-8 1-14-3-6-4-11-9-14-15-3-6-3-10 0-12z" fill="var(--ink)"/>
      <path d="M50 33a10 10 0 0 1 10 10M50 27a16 16 0 0 1 16 16" fill="none" stroke="var(--ink)" stroke-width="2" stroke-linecap="round"/>
    </svg>

    <p class="contact-phone">(888) BRISQEL-GO</p>
    <p class="contact-web">www.<span class="contact-web__domain">trybrisqel</span>.com</p>
    <p class="license">TWQB License Number: 4480512</p>
  </main>
</body>
</html>
```